Additional Benefits of Working for VELMAR

Please prepare an infographic on the additional benefits besides salary of working at VELMAR as detailed in the attached word document. Also attached is our logo in eps and our company design "Grounds". We are a Not For Profit company that finds jobs for unemployed people of government benefit payments

Target Market(s)

Attracting people to work for VELMAR. Making VELMAR an employer of choice.

Font styles to use
Sans Serif

Colors

Designer to choose colors to be used in the design.

Requirements
Must have
• be on 1 page
• have our logo
Nice to have
• Our Grounds design worked into it.
• Happy engaged employees
• Community engagement - we are a not for profit organisation
Should not have
• Discrimination, swearing,

```html
<!DOCTYPE html>
<html lang="en">
<head>
<meta charset="utf-8">
<title>The Benefits of Working with VELMAR</title>
<link href="https://fonts.googleapis.com/css2?family=Didact+Gothic&display=swap" rel="stylesheet">
<style>
  :root {
    --green-light: #9ccd5a;
    --green-mid: #74b043;
    --green-dark: #4f8a33;
    --ink: #1d1d1b;
    --paper: #ffffff;
    --backdrop: #ffffff;
    --shadow: rgba(0, 0, 0, 0.55);
  }
  * { box-sizing: border-box; margin: 0; padding: 0; }
  html, body {
    width: 1200px; height: 1166px; overflow: hidden;
    background: var(--backdrop);
    font-family: "Didact Gothic", "Century Gothic", sans-serif;
    color: var(--ink);
  }
  .sheet {
    position: absolute; left: 134px; top: 155px;
    width: 916px; height: 854px;
    background: var(--paper);
    box-shadow: 9px 10px 6px var(--shadow);
  }
  .brand {
    position: absolute; left: 27px; top: 88px;
    font-size: 50px; font-weight: 400; letter-spacing: -1px;
    color: var(--ink); line-height: 1;
  }
  .title-banner {
    position: absolute; left: 267px; top: 16px;
    width: 627px; height: 72px; border-radius: 24px;
    background: linear-gradient(90deg, var(--green-light) 0%, var(--green-mid) 55%, var(--green-dark) 100%);
    color: #fff; font-size: 44px; line-height: 72px;
    text-align: center; letter-spacing: 0.3px;
  }
  .section-tab {
    position: absolute; width: 195px; height: 33px;
    border-radius: 16px 16px 0 0;
    background: linear-gradient(90deg, var(--green-light) 0%, var(--green-mid) 60%, var(--green-dark) 100%);
    color: #fff; text-align: center;
    padding-left: 30px;
    display: flex; flex-direction: column; justify-content: center;
    font-size: 18px; line-height: 1;
  }
  .section-tab small { font-size: 10px; display: block; margin-top: 1px; }
  .section-tab.stacked { font-size: 17px; }
  .section-list {
    position: absolute; width: 195px;
    list-style: none; text-align: center;
    font-size: 11.5px; line-height: 19.5px;
  }
  .photo {
    position: absolute; width: 195px; height: 132px;
    border-radius: 20px;
  }
  .photo-meeting { background: linear-gradient(135deg, #c9c2b8, #5b5a5e 60%, #2e2e33); }
  .photo-teamhands { background: radial-gradient(circle at 55% 40%, #fff4d8, #e1b58c 45%, #6d6a6c); }
  .photo-workshop { background: linear-gradient(135deg, #e8e6e2, #b8a99a 55%, #7b7a7e); }
  .photo-laptop { background: linear-gradient(135deg, #d9d6d0, #8a7f77 55%, #3f3c3c); }
  .photo-office { background: linear-gradient(135deg, #eef0f0, #b9b4aa 55%, #5f5e5c); }
</style>
</head>
<body>
<main class="sheet">
  <div class="brand">VELMAR</div>
  <h1 class="title-banner" style="font-weight:400">The Benefits of Working with Us</h1>

  <!-- Column 1 -->
  <h2 class="section-tab" style="left:21px;top:165px;font-weight:400">Life Balance</h2>
  <ul class="section-list" style="left:21px;top:210px">
    <li>- VELMAR Day Leave. An extra day of at Christmas</li>
    <li>- BIRTHDAY Leave. A paid day off on your birthday</li>
    <li>- A day off every month as Time In Lieu</li>
    <li>- 4 weeks Annual Leave</li>
    <li>- Genereous Personal Leave</li>
    <li>- Support for parental leave for the birth or adoption of a child</li>
    <li>- Flexible work arrangements</li>
  </ul>
  <div class="photo photo-workshop" style="left:21px;top:475px" role="img" aria-label="Photo of colleagues laughing together around a workshop table"></div>
  <h2 class="section-tab" style="left:21px;top:638px;font-weight:400">Diversity &amp; Inclusion</h2>
  <ul class="section-list" style="left:21px;top:679px">
    <li>- An inclusive and diverse culture where different backgounds, experi­ences and perspectives are valued</li>
    <li>- Gender diversity. Over 50% of our workforce and our leaders are female</li>
  </ul>

  <!-- Column 2 -->
  <div class="photo photo-meeting" style="left:233px;top:124px" role="img" aria-label="Photo of a smiling team gathered around a laptop"></div>
  <h2 class="section-tab" style="left:233px;top:283px;font-weight:400">Wellbeing</h2>
  <ul class="section-list" style="left:233px;top:341px">
    <li>- Up to $450 per year to spend on Wellbeing services such as gym or yoga memberships</li>
    <li>- Free counselling services 24x7 via our Employee Assistance Program</li>
    <li>- Discount private health insurance</li>
    <li>- WHS policies which suppor a safe, inclusive work place</li>
  </ul>
  <h2 class="section-tab" style="left:233px;top:569px;font-weight:400">Benefits</h2>
  <ul class="section-list" style="left:233px;top:628px">
    <li>- Discounted vouchers for Grocera, Freshway, Sonix, Reelhouse, Cellar Co, ValueMart, Outdoor Hub and many others via Perkwise e-wallet</li>
    <li>- A range of other employee discounts are also available, includ­ing access to discounted bankin and finance, vehicle purchasing, leasing and hotel accomodation</li>
  </ul>

  <!-- Column 3 -->
  <h2 class="section-tab stacked" style="left:451px;top:125px;font-weight:400">Career Growth<small>&amp;Professional Development</small></h2>
  <ul class="section-list" style="left:451px;top:178px">
    <li>- Ongoing internal training and development opportunities</li>
    <li>- External srudy support @ study leave</li>
    <li>- Access to the tools and technology to do your job well</li>
    <li>- Career advancement opportuni­ties</li>
    <li>- Internal job vacancy listing</li>
  </ul>
  <div class="photo photo-laptop" style="left:451px;top:379px" role="img" aria-label="Photo of coworkers discussing work at a laptop"></div>
  <h2 class="section-tab" style="left:451px;top:543px;font-weight:400">Recognition</h2>
  <ul class="section-list" style="left:451px;top:595px">
    <li>- We celebrate our people forreach­ing service milestones</li>
    <li>- Team &amp; individual recognition for high performance</li>
  </ul>
  <div class="photo photo-office" style="left:451px;top:695px" role="img" aria-label="Photo of a smiling employee at a desk in a bright office"></div>

  <!-- Column 4 -->
  <div class="photo photo-teamhands" style="left:669px;top:124px" role="img" aria-label="Photo of a team joining hands in a circle in sunlight"></div>
  <h2 class="section-tab stacked" style="left:669px;top:282px;font-weight:400">Remuneration<small>&amp; Salary Packaging</small></h2>
  <ul class="section-list" style="left:669px;top:339px">
    <li>- Competetive salary</li>
    <li>- Ability to salary package up to $15,900 and reduce your tax. Package rent, home loans, child care and much more</li>
    <li>- Salary package up to $2,650 on meal entertainment and holiday accommodation</li>
  </ul>
  <h2 class="section-tab stacked" style="left:669px;top:540px;font-weight:400">Contributing to<small>Community</small></h2>
  <ul class="section-list" style="left:669px;top:597px">
    <li>- Team involvement in local charity and community events</li>
    <li>- Participation in VELMAR's 1000 Jobs in 100 days</li>
    <li>- Strong relationships and connection with Indigenous Communities in support of Indigenous Emplyment</li>
  </ul>
</main>
</body>
</html>
```